Telecommunications/Power civil contractor needs business card design

Were a new telecommunications/power underground civil contractor that is looking for a new business card design. Our company colours are silver or grey and orange. Feel free to use the white background logo or the black background logo.

Target Market(s)

Local contractors, utility companies, private sector mining/energy companies, developers.

Industry/Entity Type

Telecommunications

Contact Information for Business Card

Each card will need the following info:
Persons name:
Title:
E-mail:
Phone number:
Shop Address:
Mailing Address:

Requirements
Must have
• Each card will need the following info:
• Persons name:
• Title:
• E-mail:
• Phone number:
• Shop Address:
• Mailing Address:

```html
<!DOCTYPE html>
<html lang="en">
<head>
<meta charset="utf-8">
<title>Tern Line Contracting Inc — Business Card</title>
<link rel="stylesheet" href="https://fonts.googleapis.com/css2?family=Lato:ital,wght@0,400;0,700;1,400&display=swap">
<style>
  :root {
    --page: #d9dbdd;
    --panel-dark: #0d0d0d;
    --panel-dark-edge: #1f1f1f;
    --panel-light: #eef0f1;
    --orange: #c7391a;
    --brand-orange: #e0531f;
    --silver: #8a8c8f;
    --ink: #1a1a1a;
    --stripe: #bfc1c3;
  }
  * { margin: 0; padding: 0; box-sizing: border-box; }
  html, body { width: 1200px; height: 970px; overflow: hidden; }
  body {
    background: var(--page);
    font-family: "Lato", sans-serif;
    position: relative;
  }
  .card {
    position: absolute;
    left: 100px; top: 184px;
    width: 1000px; height: 602px;
    display: flex;
    box-shadow: 0 10px 30px rgba(0,0,0,0.18);
  }
  .card__brand {
    width: 480px; height: 100%;
    background: linear-gradient(160deg, var(--panel-dark-edge), var(--panel-dark) 60%);
    position: relative;
  }
  .brand-mark {
    position: absolute;
    left: 150px; top: 110px;
    width: 200px; height: 200px;
  }
  .brand-name {
    position: absolute;
    left: 0; right: 0; top: 350px;
    text-align: center;
    color: var(--brand-orange);
    font-weight: 700;
    letter-spacing: 2px;
    line-height: 1.15;
  }
  .brand-name__main { display: block; font-size: 50px; }
  .brand-name__sub { display: block; font-size: 27px; letter-spacing: 3px; }
  .card__divider {
    width: 24px; height: 100%;
    background:
      linear-gradient(90deg,
        var(--panel-light) 0 4px,
        #222 4px 8px,
        var(--panel-light) 8px 12px,
        #222 12px 16px,
        var(--panel-light) 16px 18px,
        var(--stripe) 18px 24px);
  }
  .card__details {
    flex: 1;
    background: var(--panel-light);
    position: relative;
  }
  .person { position: absolute; left: 77px; top: 82px; }
  .person__name { color: var(--orange); font-weight: 700; font-size: 33px; }
  .person__title { color: var(--ink); font-style: italic; font-size: 24px; margin-top: 4px; }
  .contact { position: absolute; left: 80px; top: 212px; list-style: none; }
  .contact__item {
    display: flex; align-items: center; gap: 16px;
    font-size: 23px; color: var(--ink); height: 46px;
  }
  .contact__icon { width: 22px; height: 22px; flex: none; }
  .address { position: absolute; left: 80px; color: var(--orange); font-weight: 700; font-size: 22px; line-height: 1.4; }
  .address--mailing { top: 318px; }
  .address--shop { top: 432px; }
  .address__label { color: var(--ink); font-weight: 400; font-style: italic; font-size: 21px; margin-left: -4px; }
</style>
</head>
<body>
  <section class="card">
    <div class="card__brand">
      <svg class="brand-mark" viewBox="0 0 200 200" aria-hidden="true">
        <circle cx="100" cy="100" r="92" fill="none" stroke="var(--silver)" stroke-width="8"/>
      </svg>
      <p class="brand-name">
        <span class="brand-name__main">TERN LINE</span>
        <span class="brand-name__sub">CONTRACTING INC</span>
      </p>
    </div>
    <div class="card__divider"></div>
    <div class="card__details">
      <div class="person">
        <h1 class="person__name">Daniel Harwick</h1>
        <p class="person__title">Chief Operating Officer</p>
      </div>
      <ul class="contact">
        <li class="contact__item">
          <svg class="contact__icon" viewBox="0 0 24 24" aria-hidden="true">
            <path fill="var(--orange)" d="M3 8c0-2 4-4 9-4s9 2 9 4v2h-5V8H8v2H3z"/>
            <path fill="var(--orange)" d="M6 11h12l2 9H4z"/>
            <circle cx="12" cy="15" r="2.5" fill="var(--panel-light)"/>
          </svg>
          <span>412-555-0186</span>
        </li>
        <li class="contact__item">
          <svg class="contact__icon" viewBox="0 0 24 24" aria-hidden="true">
            <rect x="2" y="5" width="20" height="14" fill="var(--orange)"/>
            <path d="M2 5l10 8 10-8" fill="none" stroke="var(--panel-light)" stroke-width="1.8"/>
          </svg>
          <span>enquiries@ternlinecontracting.com</span>
        </li>
      </ul>
      <address class="address address--mailing">
        #1840 Calder Avenue,<br>Brookhollow, New York<br>
        <span class="address__label">(Mailing Address)</span>
      </address>
      <address class="address address--shop">
        52 Ashby Drive,<br>Fernridge, PA 15230<br>
        <span class="address__label">(Shop Address)</span>
      </address>
    </div>
  </section>
</body>
</html>
```